I need a SEO-friendly Wordpress website (making sure to style H1, H2, H3, etc correctly) for a Hawaii-based law firm called Meridian Crest Legal Group. Comparable websites include https://brvlaw.example/ and https://www.lomrit.example/ for design reference. The current copy on the TarnAdvocate.example website can be used.

```html
<!DOCTYPE html>
<html lang="en">
<head>
<meta charset="utf-8">
<title>Meridian Crest Legal Group — Kona Lawyers</title>
<link rel="stylesheet" href="https://fonts.googleapis.com/css2?family=Montserrat:wght@400;500;600;700&display=swap">
<style>
:root{
  --brown:#6b1e05;
  --rust:#9e3f0c;
  --title:#7a2a0a;
  --orange:#a8470f;
  --ink:#222;
  --text:#333;
  --light:#f4f4f4;
  --footer:#1f1f1f;
  --white:#fff;
}
*{box-sizing:border-box;margin:0;padding:0}
html,body{width:1200px;height:3767px;overflow:hidden}
body{font-family:"Montserrat",sans-serif;color:var(--text);background:var(--white);position:relative}
.abs{position:absolute}
a{color:inherit;text-decoration:none}
.topbar{left:0;top:0;width:1200px;height:41px;background:var(--brown);color:var(--white);font-size:13px}
.topbar .mail{left:90px;top:0;height:41px;line-height:41px;padding:0 10px;border-left:1px solid rgba(255,255,255,.25);border-right:1px solid rgba(255,255,255,.25)}
.topbar .addr{right:90px;top:0;height:41px;line-height:41px;padding:0 10px;font-size:11px;border-left:1px solid rgba(255,255,255,.25);border-right:1px solid rgba(255,255,255,.25)}
.header{left:0;top:41px;width:1200px;height:110px}
.brand{left:90px;top:32px;font-size:33px;font-weight:600;color:var(--title)}
.call{left:655px;top:32px;display:flex;gap:12px;align-items:center}
.call small{display:block;color:var(--rust);font-size:13px;font-weight:600}
.call span{font-size:16px;color:var(--ink)}
.social{left:876px;top:30px;display:flex;gap:10px}
.social i{display:block;width:52px;height:52px;border-radius:50%;background:var(--orange)}
.nav{left:0;top:151px;width:1200px;height:66px;background:var(--light);border-top:1px solid #ddd}
.nav ul{list-style:none;display:flex;gap:46px;position:absolute;left:90px;top:24px;font-size:16px;color:var(--ink)}
.nav .cta{left:865px;top:0;width:245px;height:66px;background:var(--orange);color:var(--white);font-size:16px;text-align:center;line-height:66px}
.hero{left:0;top:217px;width:1200px;height:537px;background:linear-gradient(100deg,#5a5048 0%,#8c8176 40%,#c9c3bb 70%,#e6e2dc 100%)}
.hero h1{left:642px;top:110px;width:480px;font-size:33px;font-weight:500;color:var(--rust);line-height:50px}
.hero p{left:644px;top:215px;width:466px;font-size:17px;line-height:35px;color:var(--ink);text-align:justify}
.card{background:var(--white);box-shadow:0 2px 14px rgba(0,0,0,.18);text-align:center}
.card .ph{margin:26px auto 0;width:262px;height:175px}
.card h3{font-size:19px;font-weight:600;color:var(--rust);margin-top:22px}
.card p{font-size:12px;line-height:27px;padding:4px 26px 0}
.card a{display:block;font-weight:600;color:var(--rust);font-size:16px;margin-top:6px}
.dots{left:565px;top:1055px;display:flex;gap:7px}
.dots i{display:block;width:18px;height:18px;border-radius:50%;background:var(--brown)}
.dots i.off{background:none;border:2px solid var(--brown)}
h2.sec{width:1200px;text-align:center;font-size:34px;font-weight:500;color:var(--title)}
.about-sub{left:0;top:1178px;width:1200px;text-align:center;font-size:24px;color:var(--rust);font-weight:500}
.about-p{left:170px;top:1225px;width:860px;text-align:center;font-size:14px;line-height:36px;color:var(--ink)}
.serve h3{left:88px;top:1370px;font-size:25px;font-weight:500;color:var(--rust);line-height:40px}
.serve p{left:90px;top:1458px;width:545px;font-size:14px;line-height:36px;text-align:justify;color:var(--ink)}
.btn{left:90px;top:1796px;width:377px;height:55px;border-radius:28px;background:var(--brown);color:var(--white);font-size:14px;font-weight:600;text-align:center;line-height:55px}
.ring{left:676px;top:1399px;width:450px;height:450px;border-radius:50%;border:5px solid var(--brown);padding:12px}
.ring div{width:100%;height:100%;border-radius:50%;background:radial-gradient(circle at 50% 40%,#8a8d92,#2b3442)}
.practice{left:0;top:1903px;width:1200px;height:633px;background:linear-gradient(#ecedee,#dfe1e3)}
.practice .lead{left:210px;top:103px;width:780px;text-align:center;font-size:13px;line-height:26px;color:var(--ink)}
.tile{width:322px;height:194px}
.tile.hl{background:linear-gradient(135deg,#b8642a,#8a3d12)}
.tile.hl div{position:absolute;left:22px;top:15px;right:22px;bottom:15px;border:1px dashed rgba(255,255,255,.7);color:var(--white);text-align:center;padding-top:62px;font-size:20px}
.tile.hl small{display:block;font-size:14px;margin-top:6px}
.post{width:328px}
.post .ph{height:194px;position:relative}
.post .date{position:absolute;left:20px;bottom:-8px;background:var(--rust);color:var(--white);font-size:14px;padding:4px 12px}
.post h3{font-size:17px;font-weight:500;color:var(--ink);margin-top:30px}
.post p{font-size:12px;line-height:25px;margin-top:8px}
.post a{display:block;font-size:14px;font-weight:600;color:var(--ink);margin-top:4px}
.testi{left:0;top:3048px;width:1200px;height:357px;background:linear-gradient(#6e230a,#80310f);color:var(--white);text-align:center}
.testi h2{margin-top:42px;font-size:32px;font-weight:600}
.testi .q{font-size:90px;line-height:70px;font-weight:700;margin-top:8px;font-family:Georgia,serif}
.testi p{width:880px;margin:14px auto 0;font-size:18px;line-height:36px}
.testi b{display:block;margin-top:14px;font-size:18px;font-weight:500}
.footer{left:0;top:3405px;width:1200px;height:362px;background:var(--footer);color:var(--white)}
.footer h4{position:absolute;top:88px;font-size:18px;font-weight:500}
.footer ul{position:absolute;top:128px;list-style:none;font-size:12px;line-height:26px}
.footer li::before{content:"›";margin-right:14px}
.contact li::before{content:none}
.email{left:838px;top:130px;width:275px;height:40px;background:var(--white);color:#888;font-size:11px;padding:13px 14px}
.sub{left:838px;top:190px;width:142px;height:40px;background:var(--rust);font-size:13px;font-weight:600;text-align:center;line-height:40px}
.copy{left:90px;top:318px;font-size:12px}
.fsoc{left:995px;top:308px;display:flex;gap:13px}
.fsoc i{display:block;width:30px;height:30px;border-radius:50%}
</style>
</head>
<body>
<div class="abs topbar">
  <div class="abs mail">✉ info@tarnadvocate.example</div>
  <div class="abs addr">📍 48-210 LANAKILA ROAD, SUITE 12 KAILUA KONA, HAWAII 96740</div>
</div>

<header class="abs header">
  <div class="abs brand">Meridian Crest Legal Group</div>
  <div class="abs call">
    <svg width="42" height="42" viewBox="0 0 42 42"><circle cx="21" cy="21" r="19" fill="none" stroke="#a8470f" stroke-width="2.5"/><path d="M14 12c2-1 3 0 4 3 1 2 0 3-1 4 1 3 3 5 6 6 1-1 2-2 4-1 3 1 4 2 3 4-1 3-4 3-7 2-5-2-9-6-10-11-1-3 0-6 1-7z" fill="#a8470f"/></svg>
    <div><small>Call us:</small><span>+1.808.555.0142</span></div>
  </div>
  <div class="abs social" aria-label="Social links"><i></i><i></i><i></i><i></i></div>
</header>

<nav class="abs nav">
  <ul><li>HOME</li><li>PRACTICE AREAS</li><li>ATTORNEYS</li><li>OUR BLOG</li><li>CONTACT US</li></ul>
  <a class="abs cta" href="#">▦ Free Consultation</a>
</nav>

<section class="abs hero" role="img" aria-label="Team of lawyers walking through an office lobby">
  <h1 class="abs">Kona Lawyers of MCLG -Legal kōkua with aloha.</h1>
  <p class="abs">Over 70 years of combined practice, specializing in: Personal Injury, Family &amp; Divorce, Child Custody Dedicated to making sure you receive the care and attention you need.</p>
</section>

<article class="abs card" style="left:99px;top:644px;width:317px;height:388px">
  <div class="ph" role="img" aria-label="Lawyers meeting clients at a desk" style="background:linear-gradient(135deg,#6b4a36,#c9b39c)"></div>
  <h3>FAMILY &amp; DIVORCE</h3>
  <p>Sed ut perspiciatis unde omnis iste natus error sit voluptatem accusantium dolorem-que laudantium cabo.</p>
  <a href="#">Read More</a>
</article>
<article class="abs card" style="left:442px;top:600px;width:317px;height:388px">
  <div class="ph" role="img" aria-label="Patient with crutches at physiotherapy" style="background:linear-gradient(135deg,#c7d4de,#3d6fa8)"></div>
  <h3>PERSONAL INJURY</h3>
  <p>Sed ut perspiciatis unde omnis iste natus error sit voluptatem accusantium dolorem-que laudantium cabo.</p>
  <a href="#">Read More</a>
</article>
<article class="abs card" style="left:785px;top:644px;width:317px;height:388px">
  <div class="ph" role="img" aria-label="Business meeting around a table" style="background:linear-gradient(135deg,#d8dadc,#4b4c50)"></div>
  <h3>REAL ESTATE</h3>
  <p>Sed ut perspiciatis unde omnis iste natus error sit voluptatem accusantium dolorem-que laudantium cabo.</p>
  <a href="#">Read More</a>
</article>
<div class="abs dots"><i class="off"></i><i></i><i></i></div>

<h2 class="abs sec" style="left:0;top:1120px">About the Kona Lawyers of MCLG</h2>
<div class="abs about-sub">Nationwide Law Firm Presence</div>
<p class="abs about-p">Kailua Kona serves as the firm's West Coast headquarters for litigation and representation on behalf of individuals and corporations involved in a wide range of legal matters. The firm and its attorneys are licensed to practice and represent clients in Hawaii, California, Arizona, Texas, and Washington D.C.</p>

<section class="serve">
  <h3 class="abs">Lawyers Serving the Big Island and<br>Neighboring Islands</h3>
  <p class="abs">The experienced attorneys in the Meridian Crest Legal Group's Kailua Kona, Hawaii office provide clients with a wide range of litigation expertise, including legal claims involving divorce &amp; family, personal injury, toxic exposures, intellectual property, and real estate.<br>Our Kona office also offers commercial and hospitality litigation expertise on behalf of a wide variety of clients, including restaurants, hotels, property owners, and many others. We never wish to see our clients go to court, though if there is no other option, you're in safe hands with our seasoned trial lawyers and the many years of courtroom experience behind them.</p>
  <a class="abs btn" href="#">Learn more about the Kona Lawyers of MCLG</a>
  <div class="abs ring"><div role="img" aria-label="Three attorneys in business suits"></div></div>
</section>

<section class="abs practice">
  <h2 class="abs sec" style="left:0;top:50px">Practice Area</h2>
  <p class="abs lead">Lorem ipsum dolor sit amet, consectetur adipiscing elit, sed do eiusmod tempor incididunt ut labore et dolore magna aliqua. Quis ipsum suspendisse ultrices gravida.</p>
  <div class="abs tile hl" style="left:98px;top:171px" role="img" aria-label="Hands of a client and lawyer"><div>Personal Injury<small>Read More ⊕</small></div></div>
  <div class="abs tile" style="left:438px;top:171px;background:linear-gradient(135deg,#e8e8e8,#3a3a3c)" role="img" aria-label="Business handshake"></div>
  <div class="abs tile" style="left:778px;top:171px;background:linear-gradient(135deg,#3a5a8a,#1c2a44)" role="img" aria-label="Team reviewing a tablet"></div>
  <div class="abs tile" style="left:98px;top:384px;background:linear-gradient(160deg,#e28a3a,#5a2410 60%,#1a0e08)" role="img" aria-label="Construction site at sunset"></div>
  <div class="abs tile" style="left:438px;top:384px;background:linear-gradient(160deg,#2a3a5a,#141a28 60%,#6a1010)" role="img" aria-label="Car accident at night"></div>
  <div class="abs tile" style="left:778px;top:384px;background:linear-gradient(135deg,#7a7470,#2a2624)" role="img" aria-label="Paramedics helping an injured person"></div>
</section>

<h2 class="abs sec" style="left:0;top:2584px">Our Blog</h2>
<article class="abs post" style="left:89px;top:2660px">
  <div class="ph" role="img" aria-label="Signing a property contract" style="background:linear-gradient(135deg,#8a8a8a,#d8d8d8)"><span class="date">▦ Oct 27 2018</span></div>
  <h3>SED UT PERSPICIATIS UND</h3>
  <p>Sed ut perspiciatis unde omnis iste natus error sit voluptatem accusantium doloremque laudantium</p>
  <a href="#">READ MORE</a>
</article>
<article class="abs post" style="left:435px;top:2660px">
  <div class="ph" role="img" aria-label="Couple consulting with a lawyer" style="background:linear-gradient(135deg,#d7c8a8,#6c6046)"><span class="date">▦ Oct 27 2018</span></div>
  <h3>SED UT PERSPICIATIS UND</h3>
  <p>Sed ut perspiciatis unde omnis iste natus error sit voluptatem accusantium doloremque laudantium</p>
  <a href="#">READ MORE</a>
</article>
<article class="abs post" style="left:782px;top:2660px">
  <div class="ph" role="img" aria-label="Colleagues talking in an office" style="background:linear-gradient(135deg,#4a5268,#c8c4c0)"><span class="date">▦ Oct 27 2018</span></div>
  <h3>SED UT PERSPICIATIS UND</h3>
  <p>Sed ut perspiciatis unde omnis iste natus error sit voluptatem accusantium doloremque laudantium</p>
  <a href="#">READ MORE</a>
</article>

<section class="abs testi">
  <h2>TESTIMONIALS</h2>
  <div class="q">“</div>
  <p>Sed ut perspiciatis unde omnis iste natus error sit voluptatem accusantium doloremque laudantium, totam rem aperiam, eaque ipsa quae ab illo inventore veritatis et quasi architecto beatae vitae dicta sunt explicabo.</p>
  <b>John Smith</b>
  <svg class="abs" style="left:66px;top:158px" width="68" height="48" viewBox="0 0 68 48"><path d="M66 24H4M26 3L4 24l22 21" fill="none" stroke="#fff" stroke-width="4"/></svg>
  <svg class="abs" style="left:1066px;top:158px" width="68" height="48" viewBox="0 0 68 48"><path d="M2 24h62M42 3l22 21-22 21" fill="none" stroke="#fff" stroke-width="4"/></svg>
</section>

<footer class="abs footer">
  <h4 style="left:92px">CONTACT US</h4>
  <ul class="contact" style="left:92px;font-size:11px;line-height:29px">
    <li>➤&nbsp;&nbsp;&nbsp;48-210 Lanakila Road, Suite 12<br>&nbsp;&nbsp;&nbsp;&nbsp;&nbsp;&nbsp;&nbsp;Kailua Kona, Hawaii 96740</li>
    <li>✆&nbsp;&nbsp;&nbsp;+1.808.555.0142</li>
    <li>✉&nbsp;&nbsp;&nbsp;clients@tarnadvocate.example</li>
  </ul>
  <h4 style="left:388px">QUICK LINKS</h4>
  <ul style="left:388px"><li>Home</li><li>Practice Areas</li><li>Attorneys</li><li>Our Blog</li><li>About Us</li><li>Contact Us</li></ul>
  <h4 style="left:612px">OTHER LINKS</h4>
  <ul style="left:612px"><li>Privacy Policy</li><li>Terms &amp; Conditions</li><li>Our Clients</li></ul>
  <h4 style="left:838px">NEWSLETTER</h4>
  <div class="abs email">Email ID</div>
  <div class="abs sub">SUBSCRIBE</div>
  <div class="abs copy">Copyrights © 2019. Allrights Reserved.</div>
  <div class="abs fsoc" aria-label="Social links"><i style="background:#2a4aa0"></i><i style="background:#1a9ad8"></i><i style="background:#c83a2a"></i></div>
</footer>
</body>
</html>
```